Summit Paw Services website design; Townsville's best active boarding kennel

I need a website for my Boarding Kennel busiess, Summit Paw Services.
I also provide additional services such as grooming, training and doggy daycare. I want to emphasize that I am a small, boutique kennel, offering quality one on one care and attention to each dog daily.
I specialise mainly in working dog type breeds and again place emphasise on dogs remaining "active" and "stimulated" during their stay.
I want to play on the emotion of people who treat their dogs like their own children.
My current business card is in bright orange and black

Target Market(s)

Target market is anyone who owns a dog.

Industry/Entity Type

Training

Number of Pages Required

5+ page

Font styles to use
Script

Requirements
Must have
• online booking form
• Location Map; 42 Marlow Rd, Cape Bexley QLD 4892
• Opening hours; 6am - 6pm
• New page tabs; grooming, training, boarding & daycare, a gallery page
• Small "ABOUT ME" SECTION: I am a registered breeder of border collies with Canine Guild Australia, qualified canine behaviourist and accomplished animal groomer.
Nice to have
• slideshow of gallery photos on the main page
• Flashing RECIEVE A FREE HYDROBATH WITH EVERY STAY

```html
<!DOCTYPE html>
<html lang="en">
<head>
<meta charset="utf-8">
<title>Summit Paw Services</title>
<link href="https://fonts.googleapis.com/css2?family=Open+Sans:wght@400;600;700;800&family=Shadows+Into+Light&display=swap" rel="stylesheet">
<style>
:root{
  --orange:#f5821f;
  --orange-deep:#e8711a;
  --black:#0c0c0c;
  --panel:#161616;
  --panel-2:#131313;
  --white:#ffffff;
  --muted:#a9a9a9;
  --field:#ffffff;
}
*{margin:0;padding:0;box-sizing:border-box}
html,body{width:760px;height:1200px;overflow:hidden;background:var(--black)}
body{position:relative;font-family:"Open Sans",Arial,sans-serif;color:var(--white)}
.abs{position:absolute}

/* header + hero */
.hero{left:0;top:0;width:760px;height:314px;background:var(--orange)}
.hero-photo{left:360px;top:40px;width:400px;height:274px;background:linear-gradient(100deg,var(--orange) 0%,#c8641c 22%,#4a3024 48%,#221c1a 70%,#3a2a22 100%)}
.nav{left:0;top:0;width:760px;height:40px;background:var(--orange);border-bottom:1px solid var(--orange-deep)}
.nav a{position:absolute;top:0;height:40px;line-height:40px;font-size:8px;color:var(--white);text-decoration:none;transform:translateX(-50%);white-space:nowrap}
.nav a.active{background:var(--black);width:62px;text-align:center;transform:none;left:148px}
.brand-tab{left:34px;top:0;width:116px;height:82px;border-radius:0 0 58px 58px;background:var(--orange)}
.brand{left:60px;top:4px;width:68px;height:68px;border-radius:50%;background:var(--white);border:3px solid var(--orange-deep);display:flex;align-items:center;justify-content:center;text-align:center;font-size:8px;font-weight:700;line-height:1.15;color:var(--black)}
.hero-title{left:62px;top:120px;font-size:30px;font-weight:800;letter-spacing:.3px;text-shadow:0 1px 2px rgba(0,0,0,.3)}
.hero-sub{left:62px;top:162px;width:320px;font-size:14.5px;font-weight:600;line-height:19px}
.btn-dark{left:62px;top:214px;width:82px;height:30px;background:var(--black);border-radius:2px;font-size:11px;font-weight:700;line-height:30px;text-align:center}
.dots{left:366px;top:295px;display:flex;gap:3px}
.dots i{width:6px;height:6px;border-radius:50%;background:var(--black)}
.dots i.on{background:var(--white)}

/* services */
.services{left:0;top:314px;width:760px;height:196px;background:var(--panel)}
.section-title{font-size:18px;font-weight:800;letter-spacing:.4px}
.service-icon{width:54px;height:54px}
.service-name{font-size:14.5px;font-weight:600;color:var(--orange);line-height:17px}
.service-text{width:200px;font-size:8px;line-height:13px;color:var(--muted)}

/* gallery + booking */
.gallery-band{left:0;top:510px;width:760px;height:316px;background:var(--black)}
.gallery{left:62px;top:565px;width:409px;height:227px;background:var(--white)}
.tile{position:absolute}
.booking{left:504px;top:540px;width:194px;height:252px;border:3px solid var(--orange)}
.booking h2{position:absolute;left:0;top:7px;width:100%;text-align:center;font-size:18px;font-weight:800}
.booking p{position:absolute;left:0;top:33px;width:100%;text-align:center;font-size:7px}
.field{position:absolute;height:20px;background:var(--field);border-radius:1px;font-size:7px;color:#888;line-height:20px;padding-left:6px}
.field .caret{position:absolute;right:0;top:0;width:12px;height:20px;border-left:1px solid #ccc;font-size:5px;text-align:center;color:#888}
.btn-book{left:30px;top:223px;width:138px;height:24px;background:var(--orange);font-size:11px;font-weight:700;text-align:center;line-height:24px}

/* promo */
.promo{left:0;top:826px;width:760px;height:156px;background:var(--panel-2)}
.promo h2{position:absolute;left:0;top:29px;width:760px;text-align:center;font-size:18px;font-weight:800}
.promo p{position:absolute;left:90px;top:58px;width:580px;text-align:center;font-size:9px;line-height:15px;color:#cfcfcf}
.signup-input{left:226px;top:931px;width:236px;height:26px;background:var(--black);font-size:7.5px;line-height:26px;padding-left:10px;color:#ddd}
.signup-btn{left:468px;top:931px;width:66px;height:26px;background:var(--orange);font-size:9px;font-weight:700;text-align:center;line-height:26px}

/* footer */
.footer{left:0;top:982px;width:760px;height:191px;background:var(--panel)}
.foot-h{font-size:12px;font-weight:700;letter-spacing:.3px}
.foot-text{font-size:7.5px;line-height:13.5px;color:#bdbdbd}
.foot-text b{color:var(--orange)}
.script{font-family:"Shadows Into Light",cursive;font-size:11px;color:#d8d8d8}
.social{width:24px;height:24px;border-radius:50%;background:var(--white);display:flex;align-items:center;justify-content:center}
.social.hot{background:var(--orange)}
.social i{width:8px;height:8px;border-radius:50%;background:var(--orange)}
.social.hot i{background:var(--white)}
.map{left:486px;top:1010px;width:212px;height:132px;background:linear-gradient(135deg,#e9e6df,#d9d5cb);border:1px solid #555}
.bottom-bar{left:0;top:1173px;width:760px;height:27px;background:var(--orange);font-size:8px;text-align:center;line-height:27px}
</style>
</head>
<body>

<section class="abs hero"></section>
<div class="abs hero-photo" role="img" aria-label="Photo of a black and white border collie lying down"></div>

<nav class="abs nav">
  <a class="active" href="#">HOME</a>
  <a href="#" style="left:251px">GROOMING</a>
  <a href="#" style="left:330px">TRAINING</a>
  <a href="#" style="left:430px">BOARDING &amp; DAYCARE</a>
  <a href="#" style="left:528px">GALLERY</a>
  <a href="#" style="left:602px">ABOUT ME</a>
  <a href="#" style="left:679px">CONTACT</a>
</nav>
<div class="abs brand-tab"></div>
<div class="abs brand">Summit<br>Paw<br>Services</div>

<h1 class="abs hero-title">SUMMIT PAW SERVICES</h1>
<p class="abs hero-sub">Phasellus molestie in nisl sed gravidauisque venenatis sapien ut velit rutrum po.</p>
<div class="abs btn-dark">READ MORE</div>
<div class="abs dots"><i></i><i></i><i class="on"></i><i></i></div>

<section class="abs services"></section>
<h2 class="abs section-title" style="left:62px;top:333px">OUR &nbsp;SERVICES</h2>

<svg class="abs service-icon" style="left:63px;top:365px" viewBox="0 0 54 54" role="img" aria-label="Grooming icon">
  <circle cx="27" cy="27" r="26" fill="#f5821f"/><circle cx="27" cy="27" r="21" fill="none" stroke="#fff" stroke-width="2.5"/>
  <circle cx="21" cy="34" r="3.5" fill="none" stroke="#fff" stroke-width="2"/><circle cx="29" cy="34" r="3.5" fill="none" stroke="#fff" stroke-width="2"/>
  <path d="M22 31l8-14M28 31l-8-14" stroke="#fff" stroke-width="2" stroke-linecap="round"/>
  <path d="M34 16v22M34 18h4M34 22h4M34 26h4M34 30h4" stroke="#fff" stroke-width="1.8"/>
</svg>
<h3 class="abs service-name" style="left:126px;top:382px">Grooming<br>Services</h3>
<p class="abs service-text" style="left:62px;top:436px">offer a wide range of grooming services from hydro-baths and nail trimming to breed specific clipping and full grooming of coated breeds.</p>

<svg class="abs service-icon" style="left:282px;top:365px" viewBox="0 0 54 54" role="img" aria-label="Training icon">
  <circle cx="27" cy="27" r="26" fill="#f5821f"/><circle cx="27" cy="27" r="21" fill="none" stroke="#fff" stroke-width="2.5"/>
  <circle cx="27" cy="27" r="10" fill="none" stroke="#fff" stroke-width="2"/><circle cx="27" cy="27" r="5" fill="none" stroke="#fff" stroke-width="2"/>
  <circle cx="27" cy="27" r="1.8" fill="#fff"/>
</svg>
<h3 class="abs service-name" style="left:346px;top:382px">Training<br>Services</h3>
<p class="abs service-text" style="left:282px;top:436px">Does your best friend require some training while they are here? &nbsp;I can factor in tailored training sessions to work on general manners</p>

<svg class="abs service-icon" style="left:505px;top:365px" viewBox="0 0 54 54" role="img" aria-label="Daycare icon">
  <circle cx="27" cy="27" r="26" fill="#f5821f"/><circle cx="27" cy="27" r="21" fill="none" stroke="#fff" stroke-width="2.5"/>
  <circle cx="27" cy="27" r="6" fill="#fff"/>
  <path d="M27 14v5M27 35v5M14 27h5M35 27h5M18 18l3.5 3.5M32.5 32.5L36 36M36 18l-3.5 3.5M21.5 32.5L18 36" stroke="#fff" stroke-width="2" stroke-linecap="round"/>
</svg>
<h3 class="abs service-name" style="left:568px;top:382px">Doggy<br>Daycare</h3>
<p class="abs service-text" style="left:504px;top:436px">Does your best friend require some training while they are here? &nbsp;I can factor in tailored training sessions to work on general manners</p>

<section class="abs gallery-band"></section>
<h2 class="abs section-title" style="left:62px;top:533px">PHOTO GALLERY</h2>

<div class="abs gallery">
  <div class="tile" role="img" aria-label="Dogs playing in mud" style="left:2px;top:2px;width:156px;height:131px;background:linear-gradient(160deg,#7b8a5a,#8d6a4a)"></div>
  <div class="tile" role="img" aria-label="Owner sitting with dogs on grass" style="left:160px;top:2px;width:122px;height:131px;background:linear-gradient(160deg,#8a9470,#6f7a4a)"></div>
  <div class="tile" role="img" aria-label="Border collie swimming" style="left:284px;top:2px;width:123px;height:78px;background:linear-gradient(160deg,#7d8a86,#5f6c68)"></div>
  <div class="tile" role="img" aria-label="Black dog wading in water" style="left:2px;top:135px;width:156px;height:90px;background:linear-gradient(160deg,#5a6e6a,#3e4a46)"></div>
  <div class="tile" role="img" aria-label="Brown and white border collie" style="left:160px;top:135px;width:122px;height:90px;background:linear-gradient(160deg,#7f7a55,#6a5a42)"></div>
  <div class="tile" role="img" aria-label="Pack of dogs at a waterhole" style="left:284px;top:82px;width:123px;height:143px;background:linear-gradient(160deg,#7e8c80,#5e6a5c)"></div>
  <svg class="tile" style="left:367px;top:185px" width="40" height="40" viewBox="0 0 40 40">
    <polygon points="40,0 40,40 0,40" fill="#f5821f"/>
    <path d="M27 27h8M31 23v8" stroke="#fff" stroke-width="2"/>
  </svg>
</div>

<form class="abs booking">
  <h2>ONLINE BOOKING</h2>
  <p>PLEASE FILL OUT THE BELOW FORM</p>
  <div class="field" style="left:9px;top:59px;width:81px">First Name</div>
  <div class="field" style="left:99px;top:59px;width:80px">Last Name</div>
  <div class="field" style="left:9px;top:87px;width:170px">Email Address</div>
  <div class="field" style="left:9px;top:114px;width:170px">Phone Number</div>
  <div class="field" style="left:9px;top:141px;width:81px">&#9638; &nbsp;Date<span class="caret">&#9660;</span></div>
  <div class="field" style="left:99px;top:141px;width:80px">&#9719; &nbsp;Time<span class="caret">&#9660;</span></div>
  <div class="field" style="left:9px;top:168px;width:170px;height:49px;line-height:16px;padding-top:2px">Message</div>
  <div class="abs btn-book">ONLINE BOOKING</div>
</form>

<section class="abs promo">
  <h2>RECIEVE A FREE HYDROBATH WITH EVERY STAY PHOTO GALLERY</h2>
  <p>raesent vel ultricies sapien. Phasellus molestie in nisl sed gravida.raesent vel ultricies sapien. Phasellus molestie in nisl sed gravida.<br>Quisque venenatis sapien ut velit rutrum po. Suspendisse ultrices nec enim sed semperorbi faucibus convallis arcse.</p>
</section>
<div class="abs signup-input">Email Address</div>
<div class="abs signup-btn">SIGN UP</div>

<footer class="abs footer"></footer>
<h3 class="abs foot-h" style="left:62px;top:1007px">OUR SPECIALISATION</h3>
<p class="abs foot-text" style="left:64px;top:1034px;width:190px">I specialise mainly in working dog type breeds and again place emphasise on dogs remaining <b>"active"</b> and <b>"stimulated"</b> during their stay</p>
<h3 class="abs foot-h" style="left:62px;top:1089px">FOLLOW US</h3>
<div class="abs social" style="left:62px;top:1119px" role="img" aria-label="Feed">
  <svg width="10" height="10" viewBox="0 0 10 10"><circle cx="1.5" cy="8.5" r="1.3" fill="#f5821f"/><path d="M1 5a4 4 0 0 1 4 4M1 1.5a7.5 7.5 0 0 1 7.5 7.5" fill="none" stroke="#f5821f" stroke-width="1.4"/></svg>
</div>
<div class="abs social hot" style="left:92px;top:1119px" role="img" aria-label="Social link"><i></i></div>
<div class="abs social" style="left:122px;top:1119px" role="img" aria-label="Social link"><i></i></div>
<div class="abs social" style="left:151px;top:1119px" role="img" aria-label="Social link"><i></i></div>
<div class="abs social" style="left:181px;top:1119px" role="img" aria-label="Social link"><i></i></div>
<div class="abs social" style="left:214px;top:1119px" role="img" aria-label="Email">
  <svg width="11" height="8" viewBox="0 0 11 8"><rect x="0" y="0" width="11" height="8" rx="1" fill="#f5821f"/><path d="M0.5 0.8L5.5 4.6L10.5 0.8" fill="none" stroke="#fff" stroke-width="1"/></svg>
</div>

<h3 class="abs foot-h" style="left:309px;top:1007px">LOCATION</h3>
<p class="abs script" style="left:309px;top:1025px">Contact us right now!</p>
<p class="abs foot-text" style="left:309px;top:1051px">42 Marlow Rd, Cape Bexley QLD 4892</p>
<h3 class="abs foot-h" style="left:309px;top:1090px">HAPPY HOUR</h3>
<p class="abs script" style="left:309px;top:1108px">Contact us right now!</p>
<p class="abs foot-text" style="left:309px;top:1134px">Monday &nbsp;to Sunday: &nbsp;6am - 6pm</p>

<div class="abs map" role="img" aria-label="Street map showing the kennel location"></div>

<div class="abs bottom-bar">© 2014 &nbsp;Summit Paw Services. all rights reserved privacy policy &nbsp;| &nbsp;Terms and conditions</div>

</body>
</html>
```